App UI design needed! For a Password Management Tool

Need a design of a Hostline desktop application which is a Password Management Tool, similar to 9tidewell, Quillmark or Brimsoft, with Business/Enterprise functionalities. Here attached are a few sample pages of Quillmark, and some sample pages of our app called Veltrika. We certainly want to redesign our app.
We need: 1. The layout of the web: top banner, menu, main pane; 2. Form style, main form and sub forms; 3. List style; 4 Fonts and buttons; 5. Logo.
The design should look professional, can attract business customers as well as individual users, and present a strong sense of “Security”. The look and feel should differentiate from well-known products like 9tidewell, Quillmark, Brimsoft, etc.

```html
<!DOCTYPE html>
<html lang="en">
<head>
<meta charset="utf-8">
<title>Veltrika – Password Manager UI</title>
<link href="https://fonts.googleapis.com/css2?family=Lato:wght@400;700;900&display=swap" rel="stylesheet">
<style>
:root{
  --bg-top:#5d5d5d;
  --bg-bottom:#3a3a3a;
  --brand:#0a93f0;
  --titlebar:#2a2c31;
  --sidebar:#1f2125;
  --main:#1b1d20;
  --divider:#2c2e33;
  --card:#25272b;
  --field:#202226;
  --table-head:#303237;
  --row:#2a2c30;
  --text:#ffffff;
  --muted:#d6d8dc;
  --controls:#1c1e21;
}
*{box-sizing:border-box;margin:0;padding:0}
html,body{width:1082px;height:1200px;overflow:hidden}
body{position:relative;font-family:'Lato',sans-serif;color:var(--text);
  background:linear-gradient(180deg,var(--bg-top),var(--bg-bottom))}
.backdrop-curve{position:absolute;left:0;top:0}
.window{position:absolute;left:106px;width:869px;height:518px;background:var(--main);overflow:hidden}
.window--vault{top:65px}
.window--admin{top:618px}
.titlebar{position:absolute;left:0;top:0;width:100%;height:50px;background:var(--titlebar)}
.logo{position:absolute;left:21px;top:15px;display:flex;align-items:center;gap:6px;font-size:14px;font-weight:700;color:var(--brand)}
.logo-dot{width:14px;height:14px;border-radius:50%;border:2px solid var(--brand)}
.org-name{position:absolute;left:179px;top:15px;font-size:14.5px;font-weight:700;white-space:nowrap}
.tool-btn{position:absolute;top:9px;width:32px;height:32px;border-radius:50%;border:1.5px solid var(--brand);display:flex;align-items:center;justify-content:center}
.tool-btn--on{background:var(--brand)}
.tool-btn svg{width:15px;height:15px}
.win-controls{position:absolute;left:769px;top:11px;width:91px;height:29px;border-radius:15px;background:var(--controls);display:flex;align-items:center;justify-content:space-around;padding:0 6px}
.win-controls svg{width:12px;height:12px}
.sidebar{position:absolute;left:0;top:50px;width:142px;height:468px;background:var(--sidebar);border-right:4px solid var(--divider)}
.nav-item{position:absolute;left:0;width:138px;height:29px;line-height:29px;font-size:11px;font-weight:700;white-space:nowrap}
.nav-item--sub{font-weight:400}
.nav-item--active{background:var(--brand)}
.nav-item .label{position:absolute;left:57px;white-space:nowrap}
.nav-item .label--tight{letter-spacing:-.25px}
.nav-item .toggle{position:absolute;left:14px;font-weight:900}
.nav-item svg,.nav-item .org-mark{position:absolute;left:25px;top:8px;width:13px;height:13px}
.org-mark{border-radius:50%;background:#5a4fb0}
.page-title{position:absolute;left:179px;top:84px;font-size:30px;font-weight:900;letter-spacing:-.3px;white-space:nowrap}
.card{position:absolute;left:179px;top:149px;width:659px;height:312px;background:var(--card);border-radius:7px}
.entry-list{position:absolute;left:0;top:0;width:208px;height:100%;border-right:1px solid var(--divider)}
.entry{position:absolute;left:2px;width:206px;height:40px}
.entry--selected{background:var(--brand)}
.entry-icon{position:absolute;left:22px;top:6px;width:28px;height:28px;border-radius:50%;border:2px solid #fff;display:flex;align-items:center;justify-content:center}
.entry-text{position:absolute;left:62px;top:5px;font-size:10px;line-height:15.5px;white-space:nowrap}
.detail-head{position:absolute;left:231px;top:34px;display:flex;align-items:center;gap:11px;font-size:19px;font-weight:700}
.detail-mark{width:25px;height:25px;border-radius:50%;border:2px solid #fff}
.detail-actions{position:absolute;left:593px;top:40px;font-size:9px;display:flex;align-items:center;gap:5px}
.detail-more{position:absolute;left:640px;top:38px}
.field{position:absolute;left:231px;width:414px;height:30px;background:var(--field);border-radius:3px;font-size:9px;line-height:30px;padding-left:22px}
.search{position:absolute;left:27px;top:25px;width:415px;height:32px;border:1px solid #3a3c41;border-radius:3px;background:var(--field)}
.search svg{position:absolute;left:22px;top:10px;width:11px;height:11px}
.new-btn{position:absolute;left:452px;top:29px;width:54px;height:23px;border-radius:12px;background:var(--brand);font-size:10px;display:flex;align-items:center;justify-content:center;gap:3px}
.table{position:absolute;left:27px;top:62px;width:607px}
.table-row{position:absolute;left:0;width:607px;height:31px;font-size:10.5px;line-height:31px;background:var(--row)}
.table-row--head{top:0;height:30px;line-height:30px;background:var(--table-head)}
.table-row span{position:absolute;white-space:nowrap}
.pager{position:absolute;top:210px;height:23px;font-size:10.5px;font-weight:700;line-height:23px;white-space:nowrap}
.pager-page{background:var(--brand);width:23px;text-align:center}
.pager-size{background:var(--field);width:55px;text-align:center}
</style>
</head>
<body>

<svg class="backdrop-curve" width="1082" height="1200" viewBox="0 0 1082 1200" aria-hidden="true">
  <path d="M0,128 Q130,330 150,640 Q152,960 78,1200 L0,1200 Z" fill="#0a93f0"/>
</svg>

<!-- Vault window -->
<section class="window window--vault">
  <header class="titlebar">
    <div class="logo"><span class="logo-dot"></span>Veltrika</div>
    <div class="tool-btn tool-btn--on" style="left:563px"><svg viewBox="0 0 16 16"><path d="M8 2 1 8h2v6h4v-4h2v4h4V8h2z" fill="#fff"/></svg></div>
    <div class="tool-btn" style="left:605px"><svg viewBox="0 0 16 16" stroke="#fff" stroke-width="1.3" fill="none"><path d="M2 3h12M3 6h10M2 9h12M3 12h10M2 14.5h12"/></svg></div>
    <div class="tool-btn" style="left:648px"><svg viewBox="0 0 16 16" fill="none" stroke="#fff" stroke-width="1.3"><path d="M4 11V7a4 4 0 0 1 8 0v4l1.5 1.5h-11z M6.5 14h3"/></svg></div>
    <div class="tool-btn" style="left:690px"><svg viewBox="0 0 16 16" fill="#fff"><circle cx="8" cy="3" r="1.3"/><circle cx="8" cy="8" r="1.3"/><circle cx="8" cy="13" r="1.3"/></svg></div>
    <div class="win-controls">
      <svg viewBox="0 0 12 12"><rect x="0" y="5" width="12" height="2.2" fill="#fff"/></svg>
      <svg viewBox="0 0 12 12"><rect x="0" y="0" width="12" height="12" fill="#fff"/></svg>
      <svg viewBox="0 0 12 12" stroke="#fff" stroke-width="2.4"><path d="M1 1l10 10M11 1 1 11"/></svg>
    </div>
  </header>

  <nav class="sidebar">
    <div class="nav-item" style="top:20px"><svg viewBox="0 0 16 16" fill="none" stroke="#ccc" stroke-width="1.1"><path d="M8 1.5l2 4.3 4.6.5-3.4 3.1 1 4.6L8 11.7 3.8 14l1-4.6L1.4 6.3l4.6-.5z"/></svg><span class="label">Favourites</span></div>
    <div class="nav-item" style="top:51px"><span class="toggle">-</span><span class="org-mark"></span><span class="label">ORVN</span></div>
    <div class="nav-item nav-item--active" style="top:82px"><svg viewBox="0 0 16 16" fill="none" stroke="#fff" stroke-width="1.1"><circle cx="10.5" cy="5.5" r="3.5"/><path d="M8 8 2 14M4 12l2 2"/></svg><span class="label">Web Logins</span></div>
    <div class="nav-item" style="top:112px"><span class="toggle">-</span><svg viewBox="0 0 16 16" fill="none" stroke="#ccc" stroke-width="1.1"><path d="M1.5 2.5h6l7 7-5 5-7-7z"/><circle cx="4.8" cy="5.5" r="1"/></svg><span class="label">Tags</span></div>
    <div class="nav-item nav-item--sub" style="top:143px"><span class="label"># orvane tag</span></div>
    <div class="nav-item nav-item--sub" style="top:174px"><span class="label"># news</span></div>
    <div class="nav-item nav-item--sub" style="top:205px"><span class="label"># Office</span></div>
    <div class="nav-item nav-item--sub" style="top:236px"><span class="label"># Source code</span></div>
    <div class="nav-item" style="top:266px"><span class="toggle">-</span><svg viewBox="0 0 16 16" fill="none" stroke="#ccc" stroke-width="1.1"><circle cx="8" cy="5" r="3"/><path d="M2.5 14.5c0-3 2.5-5 5.5-5s5.5 2 5.5 5z"/></svg><span class="label">Personal</span></div>
    <div class="nav-item" style="top:297px"><svg viewBox="0 0 16 16" fill="none" stroke="#ccc" stroke-width="1.1"><circle cx="10.5" cy="5.5" r="3.5"/><path d="M8 8 2 14M4 12l2 2"/></svg><span class="label">Web Logins</span></div>
    <div class="nav-item" style="top:328px"><span class="toggle">-</span><svg viewBox="0 0 16 16" fill="none" stroke="#ccc" stroke-width="1.1"><path d="M1.5 2.5h6l7 7-5 5-7-7z"/><circle cx="4.8" cy="5.5" r="1"/></svg><span class="label">My Tags</span></div>
    <div class="nav-item nav-item--sub" style="top:359px"><span class="label"># Payment</span></div>
  </nav>

  <h1 class="page-title">Web Logins</h1>

  <div class="card">
    <div class="entry-list">
      <div class="entry" style="top:41px">
        <div class="entry-icon"><svg width="14" height="14" viewBox="0 0 16 16" fill="none" stroke="#fff" stroke-width="1.5"><circle cx="5" cy="11" r="3"/><path d="M7 9l7-7M11 5l2 2"/></svg></div>
        <div class="entry-text">@mailhub orvane<br>my orvane \d_okafor</div>
      </div>
      <div class="entry" style="top:106px">
        <div class="entry-icon"></div>
        <div class="entry-text">Chatterly<br>rmoreno@mailbox.test</div>
      </div>
      <div class="entry entry--selected" style="top:170px">
        <div class="entry-icon"></div>
        <div class="entry-text">Codevault<br>rmoreno@mailbox.test</div>
      </div>
      <div class="entry" style="top:230px">
        <div class="entry-icon"></div>
        <div class="entry-text">Talentra - default<br>1-r d_okafor@orvane.test</div>
      </div>
    </div>

    <div class="detail-head"><span class="detail-mark"></span>Codevault</div>
    <div class="detail-actions">Edit <svg width="9" height="9" viewBox="0 0 10 10" fill="#fff"><path d="M1 7.5 7 1.5l1.5 1.5-6 6H1z"/></svg></div>
    <svg class="detail-more" width="4" height="13" viewBox="0 0 4 13" fill="#ccc"><circle cx="2" cy="1.5" r="1"/><circle cx="2" cy="6.5" r="1"/><circle cx="2" cy="11.5" r="1"/></svg>

    <div class="field" style="top:85px">Login Username</div>
    <div class="field" style="top:121px">Login Password</div>
    <div class="field" style="top:161px">Login Page URL</div>
    <div class="field" style="top:197px">Client Container</div>
  </div>
</section>

<!-- Admin window -->
<section class="window window--admin">
  <header class="titlebar">
    <div class="logo"><span class="logo-dot"></span>Veltrika</div>
    <div class="org-name">Orvane Info Tech Co Ltd</div>
    <div class="tool-btn" style="left:563px"><svg viewBox="0 0 16 16"><path d="M8 2 1 8h2v6h4v-4h2v4h4V8h2z" fill="#fff"/></svg></div>
    <div class="tool-btn tool-btn--on" style="left:605px"><svg viewBox="0 0 16 16" stroke="#fff" stroke-width="1.3" fill="none"><path d="M2 3h12M3 6h10M2 9h12M3 12h10M2 14.5h12"/></svg></div>
    <div class="tool-btn" style="left:648px"><svg viewBox="0 0 16 16" fill="none" stroke="#fff" stroke-width="1.3"><path d="M4 11V7a4 4 0 0 1 8 0v4l1.5 1.5h-11z M6.5 14h3"/></svg></div>
    <div class="tool-btn" style="left:690px"><svg viewBox="0 0 16 16" fill="#fff"><circle cx="8" cy="3" r="1.3"/><circle cx="8" cy="8" r="1.3"/><circle cx="8" cy="13" r="1.3"/></svg></div>
    <div class="win-controls">
      <svg viewBox="0 0 12 12"><rect x="0" y="5" width="12" height="2.2" fill="#fff"/></svg>
      <svg viewBox="0 0 12 12"><rect x="0" y="0" width="12" height="12" fill="#fff"/></svg>
      <svg viewBox="0 0 12 12" stroke="#fff" stroke-width="2.4"><path d="M1 1l10 10M11 1 1 11"/></svg>
    </div>
  </header>

  <nav class="sidebar">
    <div class="nav-item" style="top:20px"><svg viewBox="0 0 16 16" fill="none" stroke="#ccc" stroke-width="1.1"><path d="M1.5 8 8 2l6.5 6M3.5 7v7h9V7M6.5 14v-4h3v4"/></svg><span class="label">Dashboard</span></div>
    <div class="nav-item" style="top:51px"><svg viewBox="0 0 16 16" fill="none" stroke="#ccc" stroke-width="1.1"><circle cx="8" cy="5.5" r="2.3"/><circle cx="3.5" cy="6.5" r="1.7"/><circle cx="12.5" cy="6.5" r="1.7"/><path d="M4 13c0-2.5 2-4 4-4s4 1.5 4 4zM1 12.5c0-1.8 1-3 2.5-3M15 12.5c0-1.8-1-3-2.5-3"/></svg><span class="label">Users</span></div>
    <div class="nav-item" style="top:82px"><svg viewBox="0 0 16 16" fill="none" stroke="#ccc" stroke-width="1.1"><circle cx="8" cy="5" r="3"/><path d="M2.5 14.5c0-3 2.5-5 5.5-5s5.5 2 5.5 5z"/></svg><span class="label">Teams</span></div>
    <div class="nav-item" style="top:112px"><svg viewBox="0 0 16 16" fill="none" stroke="#ccc" stroke-width="1.1"><path d="M1.5 2.5h6l7 7-5 5-7-7z"/><circle cx="4.8" cy="5.5" r="1"/></svg><span class="label label--tight">Client Containers</span></div>
    <div class="nav-item nav-item--active" style="top:143px"><svg viewBox="0 0 16 16" fill="none" stroke="#fff" stroke-width="1.1"><rect x="1.5" y="2.5" width="13" height="9"/><path d="M8 11.5v2.5M5 14h6"/></svg><span class="label">Web Logins</span></div>
    <div class="nav-item" style="top:174px"><svg viewBox="0 0 16 16" fill="none" stroke="#ccc" stroke-width="1.1"><path d="M8 1.5l2 4.3 4.6.5-3.4 3.1 1 4.6L8 11.7 3.8 14l1-4.6L1.4 6.3l4.6-.5z"/></svg><span class="label">Reports</span></div>
  </nav>

  <h1 class="page-title">Client Containers</h1>

  <div class="card">
    <div class="search"><svg viewBox="0 0 12 12" fill="none" stroke="#fff" stroke-width="1.8"><circle cx="5" cy="5" r="3.6"/><path d="M7.6 7.6 11 11"/></svg></div>
    <div class="new-btn"><svg width="9" height="9" viewBox="0 0 10 10" stroke="#fff" stroke-width="2"><path d="M5 0v10M0 5h10"/></svg>New</div>

    <div class="table">
      <div class="table-row table-row--head">
        <span style="left:18px">Client Containers Des..</span>
        <span style="left:228px">IP</span>
        <span style="left:394px">Remark</span>
        <span style="left:533px">Status</span>
      </div>
      <div class="table-row" style="top:39px">
        <span style="left:23px">Hostline China 10.....</span>
        <span style="left:225px">10.48.207.19</span>
        <span style="left:394px">Remark</span>
        <span style="left:534px">Status</span>
      </div>
      <div class="table-row" style="top:75px">
        <span style="left:23px">Hostline China 10.....</span>
        <span style="left:225px">10.48.207.19</span>
        <span style="left:394px">Remark</span>
        <span style="left:534px">Status</span>
      </div>
    </div>

    <div class="pager" style="left:445px">1 -2 of 2 items</div>
    <div class="pager" style="left:520px">&lt;</div>
    <div class="pager pager-page" style="left:532px">1</div>
    <div class="pager" style="left:566px">&gt;</div>
    <div class="pager pager-size" style="left:577px">20 Page</div>
  </div>
</section>

</body>
</html>
```